PixelMarrow Inc. Website & iPhone Apps Landing Pages

We need a web site design for our company. We develop software and do various consultant projects for our clients. Our products focus on the mobile platform, mainly the iPhone (business, games, social, etc.). We want to communicate that our software is simple and good as candy. The web pages should be fun to look at not loosing seriousness and credibility. Web 2.0 style and 960 grid system a must. We are opened to any overall site colour scheme suggestions (look at the sites we like below).

Must haves:
- Our logo should be seen on the site and look great on it :-) (preview attached below)
- Main home page and app landing page.
- Section links/tabs on the home page (home,apps,support,blog,contact,about)
- No text in images
- Style sheet

Looks we like:
- http://k7q3vxp9lrtwz.examplecdn.net/441_Site_Mock/final_large.jpg
- http://k7q3vxp9lrtwz.examplecdn.net/Deluxe_71_Drawn_Phone_Landing_Page/final.jpg
- http://grenmoor.com/
- http://lumbrel.ca/
- http://fairtwig.com/

Industry/Entity Type

Business

Requirements
Must have
• - Company logo should look great on pages.
• - Main home page and app landing page.
• - Section links/tabs on the home page (home,apps,support,blog,contact,about)
• - Web 2.0 style.
• - 960 grid system (12 col, 16 col).
• - Sliced ann optmized
• - Exported in all major formats (psd,ai,eps,png,jpeg,etc)
• - Style sheet
Should not have
• - Text in images

```html
<!DOCTYPE html>
<html lang="en">
<head>
<meta charset="utf-8">
<title>PixelMarrow – New App Title</title>
<link href="https://fonts.googleapis.com/css2?family=Open+Sans:wght@400;600;700&family=Outfit:wght@600;700&display=swap" rel="stylesheet">
<style>
  :root {
    --ink: #1f150e;
    --body: #2b2b2b;
    --muted: #444;
    --red: #c8141e;
    --red-dark: #a50f17;
    --dark: #2b2b2b;
    --dark-2: #343434;
    --sky-top: #ffffff;
    --sky-bottom: #c4dafa;
    --band: #a3c6f9;
    --panel: #dcdcdc;
    --panel-border: #b9b9b9;
    --strip: #f3f0f1;
    --line: #d9d9d9;
    --white: #ffffff;
  }
  * { box-sizing: border-box; margin: 0; padding: 0; }
  html, body { width: 1200px; height: 1132px; overflow: hidden; }
  body {
    position: relative;
    background: var(--white);
    font-family: "Open Sans", "Helvetica Neue", Arial, sans-serif;
    color: var(--body);
  }

  /* header */
  .site-header {
    position: absolute; left: 0; top: 0; width: 1200px; height: 67px;
    background: repeating-linear-gradient(135deg, var(--dark) 0 6px, var(--dark-2) 6px 12px);
  }
  .brand {
    position: absolute; left: 130px; top: 12px;
    display: flex; align-items: center; gap: 10px;
    font-weight: 700; font-size: 28px;
    color: var(--white); letter-spacing: -0.5px;
  }
  .brand-dot { width: 22px; height: 22px; border-radius: 50%; background: var(--red); }
  .main-nav a {
    position: absolute; top: 22px;
    color: var(--white); text-decoration: none;
    font-weight: 700; font-size: 15px;
  }
  .main-nav .current::before, .main-nav .current::after {
    color: var(--red); font-weight: 400; font-size: 20px; position: absolute; top: -5px;
  }
  .main-nav .current::before { content: "{"; left: -13px; }
  .main-nav .current::after { content: "}"; right: -13px; }

  /* hero */
  .hero {
    position: absolute; left: 0; top: 67px; width: 1200px; height: 381px;
    background: linear-gradient(var(--sky-top), var(--sky-bottom) 75%);
    border-bottom: 1px solid #cfd8e4;
  }
  .hero-rule { position: absolute; left: 0; top: 449px; width: 1200px; height: 1px; background: #9a9a9a; }
  .app-title {
    position: absolute; left: 129px; top: 104px;
    font-family: "Outfit", "Century Gothic", sans-serif; font-weight: 700;
    font-size: 47px; color: var(--ink); letter-spacing: -0.5px;
  }
  .tab {
    position: absolute; top: 184px; width: 120px; height: 30px;
    background: linear-gradient(#e0242d, var(--red-dark));
    border: 1px solid #8f0c12; border-radius: 2px;
    color: var(--white); font-weight: 700; font-size: 14px;
    text-align: center; line-height: 28px; letter-spacing: 0.3px;
  }
  .tab.active::after {
    content: ""; position: absolute; left: 52px; bottom: -11px;
    border-left: 7px solid transparent; border-right: 7px solid transparent;
    border-top: 11px solid var(--red-dark);
  }
  .intro {
    position: absolute; left: 131px; top: 242px; width: 450px;
    font-size: 15px; line-height: 24px; letter-spacing: 0.35px; color: var(--body);
  }

  .more-projects {
    position: absolute; left: 931px; top: 90px; width: 126px; height: 85px;
    border: 1px solid #c9c9c9; background: var(--white);
  }
  .more-projects .arrows {
    height: 58px; background: linear-gradient(#f4f8ff, #c6dcfa);
    border-bottom: 1px solid #cfcfcf;
  }
  .more-projects .label {
    text-align: center; font-weight: 700; font-size: 14px; color: #555; line-height: 24px;
  }

  .labelled-box { position: absolute; border: 1px solid var(--line); }
  .side-label {
    position: absolute; left: 0; top: 0; bottom: 0; width: 42px;
    background: var(--strip); border-right: 1px solid var(--line);
    display: flex; align-items: center; justify-content: center;
  }
  .side-label span {
    writing-mode: vertical-rl; transform: rotate(180deg);
    font-family: "Outfit", sans-serif; font-weight: 700; font-size: 19px;
    color: var(--ink); letter-spacing: 0.5px; white-space: nowrap;
  }
  .features { left: 612px; top: 222px; width: 458px; height: 187px; background: var(--white); }
  .feature {
    position: absolute; width: 195px; font-size: 13px; line-height: 24px;
    letter-spacing: 0.25px; color: var(--muted);
  }
  .feature strong { font-weight: 400; color: #111; }

  /* screenshots */
  .screenshots {
    left: 130px; top: 458px; width: 941px; height: 188px;
    background: var(--panel); border-color: var(--panel-border);
  }
  .screenshots .side-label { border-color: var(--panel-border); }
  .shot {
    position: absolute; top: 19px; width: 261px; height: 145px;
    background: var(--white); border: 1px solid #cfcfcf; border-radius: 2px; overflow: hidden;
  }
  .shot-fill {
    position: absolute; left: 69px; top: 9px; width: 128px; height: 136px;
    background: linear-gradient(180deg, #2a2a2a 0%, #2a2a2a 28%, #d02a32 55%, #f1d9d3 100%);
  }

  /* highlights */
  .highlight { position: absolute; width: 285px; }
  .highlight h3 {
    font-weight: 400; font-size: 19px; color: var(--red); line-height: 22px; margin-bottom: 1px;
  }
  .highlight p {
    padding-left: 2px; font-size: 13px; line-height: 24px; letter-spacing: 0.3px; color: var(--muted);
  }

  /* follow band */
  .follow {
    position: absolute; left: 0; top: 1003px; width: 1200px; height: 44px;
    background: var(--band); border-bottom: 1px solid #8db2e6;
  }
  .follow-item {
    position: absolute; top: 4px; display: flex; align-items: center; gap: 12px;
    color: var(--white); font-size: 15px; font-weight: 600; letter-spacing: 0.3px;
  }
  .follow-dot { width: 34px; height: 34px; border-radius: 50%; background: #1f5fb3; border: 2px solid #e9f1fc; }

  /* footer */
  .site-footer {
    position: absolute; left: 0; top: 1048px; width: 1200px; height: 84px;
    background: repeating-linear-gradient(135deg, var(--dark) 0 6px, var(--dark-2) 6px 12px);
  }
  .footer-nav a {
    position: absolute; top: 14px; color: var(--white); text-decoration: none;
    font-size: 13px; font-weight: 600;
  }
  .copyright {
    position: absolute; left: 0; width: 1200px; top: 43px; text-align: center;
    color: var(--white); font-size: 12px; letter-spacing: 0.3px; padding-left: 10px;
  }
</style>
</head>
<body>

<header class="site-header">
  <div class="brand"><span class="brand-dot"></span>PixelMarrow</div>
  <nav class="main-nav">
    <a href="#" style="left:621px">home</a>
    <a href="#" class="current" style="left:688px">apps</a>
    <a href="#" style="left:750px">support</a>
    <a href="#" style="left:834px">blog</a>
    <a href="#" style="left:893px">contact</a>
    <a href="#" style="left:976px">about</a>
  </nav>
</header>

<section class="hero"></section>
<div class="hero-rule"></div>

<h1 class="app-title">New App Title</h1>
<div class="tab active" style="left:143px">THE IDEA</div>
<div class="tab" style="left:298px">THE RESULT</div>

<p class="intro">Lorem ipsum dolor sit amet, consectetur adipiscing elit. Praesent erat eros, pharetra a consequat a, sagittis vel justo. Aliquam tempor felis vel orci tincidunt aliquet. Nunc sagittis, odio nec auctor tincidunt, mi neque euismod ipsum, at pretium arcu quam at nisl. Sed tellus eros, rhoncus vitae blandit quis, gravida ac felis. Aenean ante elit, ultrices non lacinia interdum, pretium in enim.</p>

<div class="more-projects">
  <div class="arrows">
    <svg width="124" height="58" viewBox="0 0 124 58" aria-hidden="true">
      <path d="M50 10 L31 28 L50 46 Z" fill="#fff" stroke="#b7c4d4"/>
      <path d="M76 10 L95 28 L76 46 Z" fill="#fff" stroke="#b7c4d4"/>
    </svg>
  </div>
  <div class="label">more projects</div>
</div>

<section class="labelled-box features">
  <div class="side-label"><span>FEATURES</span></div>
  <p class="feature" style="left:58px;top:41px"><strong>Lorem ipsum</strong> dolor sit amet, consectetur adipiscing elit.</p>
  <p class="feature" style="left:253px;top:41px">Lorem ipsum dolor sit amet, consectetur adipiscing elit.</p>
  <p class="feature" style="left:60px;top:113px">Lorem ipsum dolor sit amet, consectetur adipiscing elit.</p>
  <p class="feature" style="left:255px;top:113px">Lorem ipsum dolor sit amet, consectetur adipiscing elit.</p>
</section>

<section class="labelled-box screenshots">
  <div class="side-label"><span>SCREENSHOTS</span></div>
  <div class="shot" style="left:72px"><div class="shot-fill" role="img" aria-label="App screenshot shown on a phone"></div></div>
  <div class="shot" style="left:361px"><div class="shot-fill" role="img" aria-label="App screenshot shown on a phone"></div></div>
  <div class="shot" style="left:650px"><div class="shot-fill" role="img" aria-label="App screenshot shown on a phone"></div></div>
</section>

<article class="highlight" style="left:129px;top:682px"><h3>Highlight 1</h3><p>Lorem ipsum dolor sit amet, consectetur adipiscing elit. Quisque non ipsum enim. Nunc rhoncus pretium fringilla. Nulla id ...</p></article>
<article class="highlight" style="left:453px;top:682px"><h3>Highlight 2</h3><p>Lorem ipsum dolor sit amet, consectetur adipiscing elit. Quisque non ipsum enim. Nunc rhoncus pretium fringilla. Nulla id ...</p></article>
<article class="highlight" style="left:771px;top:682px"><h3>Highlight 3</h3><p>Lorem ipsum dolor sit amet, consectetur adipiscing elit. Quisque non ipsum enim. Nunc rhoncus pretium fringilla. Nulla id ...</p></article>
<article class="highlight" style="left:128px;top:845px"><h3>Highlight 4</h3><p>Lorem ipsum dolor sit amet, consectetur adipiscing elit. Quisque non ipsum enim. Nunc rhoncus pretium fringilla. Nulla id ...</p></article>
<article class="highlight" style="left:452px;top:845px"><h3>Highlight 5</h3><p>Lorem ipsum dolor sit amet, consectetur adipiscing elit. Quisque non ipsum enim. Nunc rhoncus pretium fringilla. Nulla id ...</p></article>
<article class="highlight" style="left:770px;top:845px"><h3>Highlight 6</h3><p>Lorem ipsum dolor sit amet, consectetur adipiscing elit. Quisque non ipsum enim. Nunc rhoncus pretium fringilla. Nulla id ...</p></article>

<div class="follow">
  <div class="follow-item" style="left:373px">Follow us on Friendlane <span class="follow-dot"></span></div>
  <div class="follow-item" style="left:627px">Follow us on Chirpline <span class="follow-dot"></span></div>
</div>

<footer class="site-footer">
  <nav class="footer-nav">
    <a href="#" style="left:261px">HOME</a>
    <a href="#" style="left:373px">APPS</a>
    <a href="#" style="left:477px">SUPPORT</a>
    <a href="#" style="left:596px">BLOG</a>
    <a href="#" style="left:720px">CONTACT</a>
    <a href="#" style="left:870px">ABOUT</a>
  </nav>
  <p class="copyright">Copyright 2010 PixelMarrow. All Rights Reserved</p>
</footer>

</body>
</html>
```